RiverPine - Rebranding, Namecard, Stationary and One Page Web

Refresh logo, make it modern and design matching name card, stationary and one page web

RiverPine Information Technology (Int'l) Company Limited
松河訊息科技(國際)有限公司

Company is System Integrator, and will be providing products and services to government and enterprise organizations. Our Chief Security Officer came from top U.S. vendor, and had been working on top enterprise and government projects globally, so we want the refreshed image of the new company to have a East Cost U.S. style, with hint of technology from Silicon Valley. The company will also be representing top brands from the U.S. on information security.

Branding refresh is needed because company is being acquired and is expanding

Target Market(s)

Cyber Security

Industry/Entity Type

Information Technology

Contact Information for Business Card

Need Chinese and English

Number of Pages Required

1 page

Font styles to use
Sans Serif

Colors
0292cd
00a990

Requirements
Must have
• Modern, clean, cyber look. Must keep same colors and general look and feel of original logo. Only modernization, do not change its personality

```html
<!DOCTYPE html>
<html lang="en">
<head>
<meta charset="utf-8">
<title>RiverPine Stationery</title>
<link href="https://fonts.googleapis.com/css2?family=Open+Sans:wght@400;600;700;800&family=Oswald:wght@500&family=Tinos&display=swap" rel="stylesheet">
<style>
  :root {
    --canvas: #f1f1f1;
    --paper: #fbfbfb;
    --edge: #e2e2e2;
    --brand-blue: #0292cd;
    --brand-sky: #2aa7de;
    --brand-green: #00a990;
    --ink: #555;
    --ink-soft: #888;
    --map: #ececec;
  }
  * { box-sizing: border-box; margin: 0; padding: 0; }
  html, body { width: 1200px; height: 1000px; overflow: hidden; }
  body { background: var(--canvas); font-family: "Open Sans", sans-serif; color: var(--ink); position: relative; }

  .sheet { position: absolute; background: var(--paper); box-shadow: 0 1px 4px rgba(0,0,0,.12); overflow: hidden; }
  .wordmark { font-family: "Open Sans", sans-serif; font-weight: 800; color: var(--brand-sky); display: flex; align-items: center; gap: .35em; white-space: nowrap; letter-spacing: .01em; }
  .wordmark .dot { width: .55em; height: .55em; border-radius: 50%; background: var(--brand-sky); }
  .wave { position: absolute; left: 0; bottom: 0; width: 100%; display: block; }
  .contact { list-style: none; font-size: 9px; line-height: 1.55; }
  .contact li { display: flex; align-items: center; gap: 6px; white-space: nowrap; }
  .contact svg { width: 8px; height: 8px; fill: var(--brand-blue); flex: none; }
  .contact .web b { color: var(--brand-blue); font-weight: 400; }

  /* notepad */
  .notepad { left: 57px; top: 132px; width: 165px; height: 228px; display: flex; justify-content: center; align-items: center; }
  .notepad .wordmark { font-size: 15px; }

  /* card back */
  .card-back { left: 27px; top: 398px; width: 279px; height: 159px; }
  .card-back .map { position: absolute; inset: 0; background: radial-gradient(ellipse at 40% 40%, var(--map), var(--paper) 75%); }
  .card-back .wordmark { position: absolute; left: 0; right: 0; top: 60px; justify-content: center; font-size: 15px; }
  .card-back .legal { position: absolute; left: 0; right: 0; top: 104px; text-align: center; color: var(--brand-blue); font-size: 7px; line-height: 1.35; font-weight: 600; }

  /* card front */
  .card-front { left: 27px; top: 595px; width: 279px; height: 160px; }
  .card-front .wordmark { position: absolute; left: 20px; top: 62px; font-size: 16px; }
  .card-front .rule { position: absolute; left: 128px; top: 34px; width: 1px; height: 76px; background: #bbb; }
  .card-front .person { position: absolute; left: 140px; top: 32px; }
  .card-front .name { color: var(--brand-blue); font-weight: 600; font-size: 11px; }
  .card-front .role { color: var(--brand-green); font-size: 8.5px; font-weight: 600; margin-bottom: 4px; }
  .card-front .addr { font-size: 6.5px; color: var(--ink-soft); line-height: 1.35; margin-bottom: 5px; }
  .card-front .contact { font-size: 6.5px; }
  .card-front .contact svg { width: 6px; height: 6px; }

  /* letterhead */
  .letterhead { left: 323px; top: 100px; width: 397px; height: 560px; }
  .letterhead .wordmark { position: absolute; left: 40px; top: 52px; font-size: 19px; }
  .letterhead .contact { position: absolute; left: 208px; top: 58px; }
  .letterhead .greeting { position: absolute; left: 40px; top: 145px; font-family: "Oswald", sans-serif; color: #8a8a8a; line-height: 1; }
  .greeting .hello { font-size: 26px; }
  .greeting .to { font-size: 13px; margin-top: 4px; }
  .letterhead .date { position: absolute; right: 44px; top: 162px; font-size: 10px; color: #555; }
  .letterhead .body { position: absolute; left: 40px; right: 40px; top: 203px; font-family: "Tinos", serif; font-size: 7.4px; line-height: 1.42; color: #444; text-align: justify; }
  .body p { margin-bottom: 9px; }
  .letterhead .office { position: absolute; left: 40px; top: 500px; display: flex; gap: 8px; font-size: 7.5px; color: var(--ink-soft); line-height: 1.45; }
  .office .label { color: var(--brand-blue); font-weight: 700; font-size: 8px; padding-right: 6px; border-right: 1px solid #aaa; align-self: center; }

  /* folder */
  .folder { left: 741px; top: 70px; width: 436px; height: 592px; }
  .folder .flap { position: absolute; right: 0; top: 0; width: 60px; height: 100%; border-left: 1px solid var(--edge); }
  .folder .wordmark { position: absolute; left: 74px; top: 282px; font-size: 36px; }

  /* envelope front */
  .envelope { left: 323px; top: 692px; width: 415px; height: 206px; }
  .envelope .wordmark { position: absolute; left: 24px; top: 48px; font-size: 15px; }
  .envelope .contact { position: absolute; left: 24px; top: 128px; font-size: 7px; }
  .envelope .contact svg { width: 6px; height: 6px; }
  .envelope .addr { position: absolute; right: 16px; top: 128px; padding-right: 6px; border-right: 1px solid var(--brand-blue); text-align: right; font-size: 7px; line-height: 1.55; color: var(--ink-soft); }

  /* envelope back */
  .envelope-back { left: 757px; top: 690px; width: 408px; height: 205px; }
  .envelope-back .flap { position: absolute; left: 0; top: 0; width: 100%; height: 56px; border-bottom: 1px solid var(--edge); border-radius: 0 0 6px 6px; }
  .envelope-back .wordmark { position: absolute; left: 0; right: 0; top: 126px; justify-content: center; font-size: 18px; }
</style>
</head>
<body>
<svg width="0" height="0" style="position:absolute">
  <defs>
    <symbol id="i-phone" viewBox="0 0 10 10"><path d="M2 0.5l2 2-1 1.2c.6 1.3 1.6 2.3 2.9 2.9L7 5.5l2 2-1.3 1.6C4.3 8.8 1.2 5.7.9 2.3z"/></symbol>
    <symbol id="i-mail" viewBox="0 0 10 10"><path d="M0 2h10v6H0zM.8 2.6L5 5.6l4.2-3" /></symbol>
    <symbol id="i-web" viewBox="0 0 10 10"><circle cx="5" cy="5" r="4.5"/></symbol>
  </defs>
</svg>

<section class="sheet notepad">
  <div class="wordmark"><span class="dot"></span>RiverPine</div>
</section>

<section class="sheet card-back">
  <div class="map" role="img" aria-label="Faint world map in light grey"></div>
  <div class="wordmark"><span class="dot"></span>RiverPine</div>
  <div class="legal">RiverPine Information Technology (Int'l) Company Limited<br>松河訊息科技(國際)有限公司</div>
</section>

<section class="sheet card-front">
  <div class="wordmark"><span class="dot"></span>RiverPine</div>
  <div class="rule"></div>
  <div class="person">
    <div class="name">Daniel Wong</div>
    <div class="role">CEO</div>
    <div class="addr">Room C, Unit 402, 4/F, Lok Fung Ind. Bldg,<br>No. 12 Tai Yip Street,<br>Kowloon Bay, Kowloon, HKSAR</div>
    <ul class="contact">
      <li><svg><use href="#i-phone"/></svg><span>(852) 5550 1234</span></li>
      <li><svg><use href="#i-mail"/></svg><span>danielwong@hkriverpine.com.hk</span></li>
      <li class="web"><svg><use href="#i-web"/></svg><span>www.<b>hkriverpine</b>.com.hk</span></li>
    </ul>
  </div>
  <svg class="wave" viewBox="0 0 279 40" height="40" preserveAspectRatio="none">
    <path d="M0 12 C70 24 140 26 279 8 L279 12 C140 30 70 28 0 16Z" fill="var(--brand-green)"/>
    <path d="M0 20 C80 30 150 30 279 12 L279 40 L0 40Z" fill="var(--brand-blue)"/>
  </svg>
</section>

<section class="sheet letterhead">
  <div class="wordmark"><span class="dot"></span>RiverPine</div>
  <ul class="contact">
    <li><svg><use href="#i-phone"/></svg><span>(852) 5550 1234</span></li>
    <li><svg><use href="#i-mail"/></svg><span>danielwong@hkriverpine.com.hk</span></li>
    <li class="web"><svg><use href="#i-web"/></svg><span>www.<b>hkriverpine</b>.com.hk</span></li>
  </ul>
  <div class="greeting"><div class="hello">HELLO</div><div class="to">MR. LEE</div></div>
  <div class="date">Date: 00 / 00 / 00</div>
  <div class="body">
    <p>Thank you for meeting with our team last week. We are pleased to share our proposal for your network security review.</p>
    <p>Our engineers will assess your current systems, identify risks and recommend practical steps to protect data across every office. The review covers firewalls, endpoint tools, access policies and staff training, and we will deliver a clear written report within three weeks of the start date.</p>
    <p>We will also provide a roadmap for future upgrades, with cost estimates and a timeline that fits your budget cycle.</p>
    <p>Please let us know a suitable date for the kickoff meeting.</p>
    <p>Should you have any questions, our project lead is available by phone or email at any time during office hours.</p>
    <p>We look forward to working with you.</p>
    <p>Thank you again for considering our services.</p>
    <p>Regards,<br>Arif Rahman.<br>02.02.2014</p>
  </div>
  <div class="office">
    <span class="label">Office</span>
    <span>Room C, Unit 402, 4/F, Lok Fung Ind. Bldg,<br>No. 12 Tai Yip Street, Kowloon Bay, Kowloon, HKSAR</span>
  </div>
  <svg class="wave" viewBox="0 0 397 32" height="32" preserveAspectRatio="none">
    <path d="M0 8 C120 0 250 2 397 10 L397 14 C250 6 120 4 0 12Z" fill="var(--brand-green)"/>
    <path d="M0 14 C120 7 250 8 397 16 L397 32 L0 32Z" fill="var(--brand-blue)"/>
  </svg>
</section>

<section class="sheet folder">
  <div class="flap"></div>
  <div class="wordmark"><span class="dot"></span>RiverPine</div>
</section>

<section class="sheet envelope">
  <div class="wordmark"><span class="dot"></span>RiverPine</div>
  <ul class="contact">
    <li><svg><use href="#i-phone"/></svg><span>(852) 5550 1234</span></li>
    <li><svg><use href="#i-mail"/></svg><span>danielwong@hkriverpine.com.hk</span></li>
    <li class="web"><svg><use href="#i-web"/></svg><span>www.<b>hkriverpine</b>.com.hk</span></li>
  </ul>
  <div class="addr">Room C, Unit 402, 4/F, Lok Fung Ind. Bldg,<br>No. 12 Tai Yip Street, Kowloon Bay,<br>Kowloon, HKSAR</div>
  <svg class="wave" viewBox="0 0 415 44" height="44" preserveAspectRatio="none">
    <path d="M0 8 C100 22 220 2 415 10 L415 16 C220 8 100 28 0 14Z" fill="var(--brand-green)"/>
    <path d="M0 16 C100 30 220 10 415 18 L415 44 L0 44Z" fill="var(--brand-blue)"/>
  </svg>
</section>

<section class="sheet envelope-back">
  <div class="flap"></div>
  <div class="wordmark"><span class="dot"></span>RiverPine</div>
</section>
</body>
</html>
```